Home Inspection Flyer

Looking to have flyer designed that features our business, services, and our contact information. There are three of us. We are all business partners and do not have a company phone number. So each of us would need to be listed on flyer along with our individual phone number. Everything you could possibly need is on our website from logo to services and contact information. https://brightmeadowhomereview.com/. If you could possible incorporate our company colors that would be great. You can find those in our logo top left hand side of website and attached. Please also include our proveritas and hobe logos ( home inspector affiliations ) on brochure as well. Those can be found on website. Please feel free to reach out with any questions.
Thanks
Dale
Updates
Looking to get a few tri fold designs. All the ones submitted have been 8x11
Look and feel

```html
<!DOCTYPE html>
<html lang="en">
<head>
<meta charset="utf-8">
<title>Brightmeadow Home Review – Inspection Flyer</title>
<link href="https://fonts.googleapis.com/css2?family=Poppins:wght@300;400;500;600;700&display=swap" rel="stylesheet">
<style>
:root{
  --bg:#e4e4e4;
  --paper:#ffffff;
  --ink:#1f1d1e;
  --dark:#2a2728;
  --green:#7dc242;
  --purple:#8a2be2;
  --text:#333;
  --photo-a:#c9b9a6;
  --photo-b:#7a8fa8;
}
*{margin:0;padding:0;box-sizing:border-box}
html,body{width:1200px;height:2409px;overflow:hidden}
body{background:var(--bg);font-family:'Poppins',sans-serif;color:var(--text);position:relative}
.flyer{position:absolute;left:50px;top:493px;width:1063px;height:1376px;background:var(--paper);
  transform:scale(1.0348);transform-origin:top left;overflow:hidden;box-shadow:0 20px 40px rgba(0,0,0,.25)}
.abs{position:absolute}
.brand{left:55px;top:110px;display:flex;align-items:center;gap:16px}
.brand-mark{width:34px;height:34px;background:var(--green)}
.brand-name{font-weight:600;font-size:30px;line-height:1.1;color:var(--ink);letter-spacing:.5px}
.hero-band{left:0;top:230px;width:1063px;height:275px;background:var(--dark)}
.hero-photo{left:505px;top:0;width:558px;height:505px;
  background:linear-gradient(160deg,#efe9e2 0%,var(--photo-a) 45%,var(--photo-b) 75%,#8b6f55 100%)}
.hero-fade{left:470px;top:230px;width:80px;height:275px;background:linear-gradient(90deg,var(--dark),rgba(42,39,40,0))}
.headline{left:55px;top:275px;font-weight:700;font-size:46px;line-height:50px;color:#fff;white-space:nowrap}
.headline .accent{color:var(--green)}
.tagline{left:53px;top:436px;height:36px;padding:0 14px 0 10px;background:var(--purple);color:#fff;
  font-weight:600;font-size:21px;line-height:36px;border-radius:4px 0 0 4px;white-space:nowrap}
.stripe{left:0;top:505px;width:1063px;height:13px;background:var(--green)}
.intro-rule{left:55px;top:535px;width:3px;height:115px;background:var(--green)}
.h2{font-weight:600;font-size:25px;color:var(--ink);line-height:30px;white-space:nowrap}
.h2 .hl{color:var(--purple)}
.intro-title{left:72px;top:538px}
.intro-body{left:72px;top:576px;width:930px;font-size:14.5px;line-height:17px;font-weight:400;color:#444}
.services-title{left:53px;top:658px}
.service{display:flex;align-items:center;gap:12px;font-size:16px;color:var(--ink);white-space:nowrap}
.service svg{width:26px;height:26px}
.thumb{width:183px;height:140px;box-shadow:5px 5px 0 var(--green),0 4px 8px rgba(0,0,0,.3)}
.benefits-title{left:53px;top:858px}
.benefits{left:55px;top:926px;list-style:none}
.benefits li{display:flex;align-items:center;gap:14px;font-size:15.5px;line-height:22.6px;color:var(--ink);white-space:nowrap}
.tick{width:15px;height:15px;flex:none}
.badge{width:160px;height:160px;border-radius:50%}
.badge-gold{left:642px;top:1025px;background:radial-gradient(circle,#f6d548 55%,#c9a01c 57%,#f6d548 62%,#b8901a 100%)}
.badge-grey{left:825px;top:1025px;background:radial-gradient(circle,#d8d3c2 50%,#3a3a3a 53%,#cfc9b4 62%,#2e2e2e 100%)}
.footer{left:0;top:1215px;width:1063px;height:161px;background:var(--dark)}
.cta{left:0;top:1215px}
.cta-text{left:55px;top:1244px;font-weight:600;font-size:27px;line-height:33px;color:#fff}
.contact{top:1240px;width:250px}
.contact .name{font-weight:500;font-size:20px;color:var(--green);margin-bottom:10px;white-space:nowrap}
.contact .row{display:flex;align-items:center;gap:8px;font-size:15px;color:#fff;line-height:24px;white-space:nowrap}
.contact .row.phone{font-size:15.5px}
.contact svg{width:15px;height:15px;flex:none}
</style>
</head>
<body>
<main class="flyer">
  <div class="abs brand">
    <span class="brand-mark"></span>
    <span class="brand-name">BRIGHTMEADOW<br>HOME REVIEW</span>
  </div>

  <div class="abs hero-band"></div>
  <div class="abs hero-photo" role="img" aria-label="Smiling family of three sitting on a living room floor holding a cardboard roof over their heads"></div>
  <div class="abs hero-fade"></div>
  <h1 class="abs headline">FAST, AFFORDABLE,<br>RELIABLE HOME<br><span class="accent">INSPECTIONS</span></h1>
  <div class="abs tagline">INSPECTIONS I CONSULTING I TESTING</div>
  <div class="abs stripe"></div>

  <div class="abs intro-rule"></div>
  <h2 class="abs h2 intro-title">What Is A Brightmeadow Home Buyer <span class="hl">Inspection?</span></h2>
  <p class="abs intro-body">A home buyer inspection is a visual examination of a home and its systems: interior plumbing, electrical, roof, attics (temperature permitting), and visible areas of walls, ceilings, floors, foundations, etc. No house is perfect. If an inspector finds a problem it is not an indication the home should not be purchased, nor does an inspection represent a work order for repairs. It simply serves to educate you as to the condition of the home.</p>

  <h2 class="abs h2 services-title">Brightmeadow <span class="hl">Inspection Services</span></h2>
  <svg width="0" height="0" style="position:absolute">
    <defs>
      <symbol id="tick" viewBox="0 0 16 16"><circle cx="8" cy="8" r="8" fill="#7dc242"/><path d="M4.5 8.3l2.3 2.3 4.7-4.8" stroke="#fff" stroke-width="2" fill="none"/></symbol>
      <symbol id="phone" viewBox="0 0 16 16"><path d="M3 1l3 3-1.5 2c1 2 3 4 5 5l2-1.5 3 3-2 2C7 14 2 9 1 3z" fill="#7dc242"/></symbol>
      <symbol id="mail" viewBox="0 0 16 16"><rect x="1" y="3" width="14" height="10" fill="#7dc242"/><path d="M1 3l7 6 7-6" stroke="#2a2728" stroke-width="1.3" fill="none"/></symbol>
    </defs>
  </svg>
  <div class="abs service" style="left:55px;top:700px"><svg viewBox="0 0 26 26"><path d="M3 13L13 4l10 9v10H3z" fill="none" stroke="#8a2be2" stroke-width="2.5"/><rect x="10" y="15" width="6" height="8" fill="#8a2be2"/></svg>Home Inspection</div>
  <div class="abs service" style="left:55px;top:736px"><svg viewBox="0 0 26 26"><circle cx="13" cy="13" r="9" fill="none" stroke="#8a2be2" stroke-width="2.5"/><circle cx="13" cy="13" r="4" fill="#8a2be2"/></svg>Pest Inspection</div>
  <div class="abs service" style="left:55px;top:774px"><svg viewBox="0 0 26 26"><circle cx="15" cy="11" r="7" fill="none" stroke="#8a2be2" stroke-width="2.5"/><path d="M10 16l-6 6" stroke="#8a2be2" stroke-width="3"/></svg>Radon Inspection</div>
  <div class="abs service" style="left:55px;top:808px"><svg viewBox="0 0 26 26"><rect x="4" y="8" width="12" height="10" rx="2" fill="#8a2be2"/><path d="M16 11l6-3v10l-6-3z" fill="#8a2be2"/></svg>Sewer Camera Inspection</div>
  <div class="abs service" style="left:340px;top:702px"><svg viewBox="0 0 26 26"><path d="M13 3C9 10 7 13 7 16a6 6 0 0012 0c0-3-2-6-6-13z" fill="#8a2be2"/></svg>Water Sample Test</div>
  <div class="abs service" style="left:340px;top:736px"><svg viewBox="0 0 26 26"><path d="M2 9q3-3 6 0t6 0 6 0 5 0M2 14q3-3 6 0t6 0 6 0 5 0M2 19q3-3 6 0t6 0 6 0 5 0" stroke="#8a2be2" stroke-width="2" fill="none"/></svg>Well Flow Test</div>
  <div class="abs service" style="left:340px;top:776px"><svg viewBox="0 0 26 26" fill="#8a2be2"><circle cx="5" cy="5" r="2"/><circle cx="13" cy="5" r="2"/><circle cx="21" cy="5" r="2"/><circle cx="5" cy="13" r="2"/><circle cx="13" cy="13" r="2"/><circle cx="21" cy="13" r="2"/><circle cx="5" cy="21" r="2"/><circle cx="13" cy="21" r="2"/><circle cx="21" cy="21" r="2"/></svg>Septic Dye Flow Test</div>

  <div class="abs thumb" style="left:615px;top:675px;background:linear-gradient(160deg,#8c9a7a,#5a5a4e 60%,#3b3a34)" role="img" aria-label="Close-up of an insect on weathered roof shingles"></div>
  <div class="abs thumb" style="left:820px;top:675px;background:radial-gradient(circle at 55% 45%,#cfd3d6,#3a3f44 55%,#15181b)" role="img" aria-label="Basement sump pit with white drain pipes"></div>
  <div class="abs thumb" style="left:615px;top:840px;background:linear-gradient(150deg,#e8ece9,#b59a5a 45%,#3c74c2 80%)" role="img" aria-label="Brass water meter with blue fittings"></div>
  <div class="abs thumb" style="left:820px;top:840px;background:linear-gradient(150deg,#ececea,#c5c3bd 55%,#6a6a68)" role="img" aria-label="Sewer inspection camera reel beside a floor drain"></div>

  <h2 class="abs h2 benefits-title">Brightmeadow Home Review's<br><span class="hl">Benefits &amp; Credentials</span></h2>
  <ul class="abs benefits">
    <li><svg class="tick"><use href="#tick"/></svg>Fast, Reliable, Affordable Pricing</li>
    <li><svg class="tick"><use href="#tick"/></svg>Available On Evenings And Weekends</li>
    <li><svg class="tick"><use href="#tick"/></svg>Agent - Realtor Access Keys</li>
    <li><svg class="tick"><use href="#tick"/></svg>48 Hour Reporting</li>
    <li><svg class="tick"><use href="#tick"/></svg>Licensed By State Of Pennsylvania</li>
    <li><svg class="tick"><use href="#tick"/></svg>Members Of Hobe Society Of Home Inspectors</li>
    <li><svg class="tick"><use href="#tick"/></svg>Members Of Proveritas Association Of Certified Home Inspectors</li>
    <li><svg class="tick"><use href="#tick"/></svg>Abide By The Hobe Code Of Ethics</li>
    <li><svg class="tick"><use href="#tick"/></svg>Continuous Learning And Professional Development</li>
    <li><svg class="tick"><use href="#tick"/></svg>Professional Level Of Liability Insurance</li>
    <li><svg class="tick"><use href="#tick"/></svg>Nationally Accredited B.S. Business &amp; Marketing Degrees</li>
    <li><svg class="tick"><use href="#tick"/></svg>Additional Services Available</li>
  </ul>

  <div class="abs badge badge-gold" role="img" aria-label="hobe membership badge"></div>
  <div class="abs badge badge-grey" role="img" aria-label="proveritas certified inspector badge"></div>

  <div class="abs footer"></div>
  <svg class="abs cta" width="200" height="161" viewBox="0 0 200 161">
    <polygon points="0,0 155,0 195,80 155,161 0,161" fill="#8a2be2"/>
    <polyline points="155,0 195,80 155,161" fill="none" stroke="#fff" stroke-width="3"/>
  </svg>
  <div class="abs cta-text">GET IN<br>TOUCH</div>

  <div class="abs contact" style="left:220px">
    <div class="name">Evan Corso</div>
    <div class="row phone"><svg><use href="#phone"/></svg>(555) 204-1187</div>
    <div class="row"><svg><use href="#mail"/></svg>evan.bmhr@mailhub.net</div>
  </div>
  <div class="abs contact" style="left:492px">
    <div class="name">Luke Hartwell</div>
    <div class="row phone"><svg><use href="#phone"/></svg>(555) 318-4620</div>
    <div class="row"><svg><use href="#mail"/></svg>luke.bmhr@mailhub.net</div>
  </div>
  <div class="abs contact" style="left:757px">
    <div class="name">Dale Varga</div>
    <div class="row phone"><svg><use href="#phone"/></svg>(555) 472-9035</div>
    <div class="row"><svg><use href="#mail"/></svg>dale.bmhr@mailhub.net</div>
  </div>
</main>
</body>
</html>
```